Business Card Design for Marketing Firm

Looking for business card design for higher end marketing firm. Clean but impressionable/trendy. We are a marketing firm that represents manufacturers in the foodservice equipment and supply industry. Our customers are end users such has hotels, restaurants, country clubs, convention centers and casinos as well as distributors of restaurants supplies and equipment, and manufacturers of foodservice equipment and supplies.
Target Market(s)
Hotels, Restaurants, Supply & Equipment Distributors, Foodservice Manufacturers
Industry/Entity Type
Foodservice/Hospitality
Contact Information for Business Card
Name, Title, Contact Number, Email, Website, Social Media, Address
Requirements
Must have
- Clean & Simple but Serious and Impressionable

```html
<!DOCTYPE html>
<html lang="en">
<head>
<meta charset="utf-8">
<title>Meridian Service Reps – Business Card</title>
<link rel="stylesheet" href="https://fonts.googleapis.com/css2?family=Noto+Serif:wght@700&family=Arimo:wght@400&display=swap">
<style>
  :root {
    --stage: #1d1d1f;
    --paper: #f4f4f3;
    --navy: #272c6b;
    --ink: #2e2e33;
    --white: #ffffff;
  }
  * { box-sizing: border-box; margin: 0; padding: 0; }
  html, body {
    width: 1200px; height: 1059px; overflow: hidden;
    background: var(--stage);
  }
  .card {
    position: absolute; left: 255px; width: 690px; height: 392px;
  }
  .card--front { top: 89px; background: var(--paper); }
  .card--back { top: 547px; background: var(--navy); }

  .accent-bar {
    position: absolute; left: 0; top: 174px; width: 18px; height: 40px;
    background: var(--navy);
  }
  .person { position: absolute; left: 39px; top: 169px; }
  .person__name {
    font-family: "Noto Serif", Georgia, serif; font-weight: 700;
    font-size: 24px; color: var(--navy); letter-spacing: 0.2px; line-height: 1;
  }
  .person__title {
    font-family: "Arimo", Arial, sans-serif; font-size: 16px;
    color: var(--ink); margin-top: 7px;
  }

  .brand {
    position: absolute; display: flex; flex-direction: column; align-items: center;
    font-family: "Noto Serif", Georgia, serif; font-weight: 700; text-align: center;
  }
  .brand__mark { border-radius: 50%; }
  .brand__name { line-height: 1.05; }
  .brand--front { left: 368px; top: 70px; width: 230px; color: var(--navy); }
  .brand--front .brand__mark { width: 26px; height: 26px; background: var(--navy); margin-bottom: 14px; }
  .brand--front .brand__name { font-size: 20px; }
  .brand--back { left: 0; right: 0; top: 150px; color: var(--white); }
  .brand--back .brand__mark { width: 44px; height: 44px; background: var(--white); margin-bottom: 22px; }
  .brand--back .brand__name { font-size: 34px; letter-spacing: 0.5px; }

  .contact {
    position: absolute; left: 368px; top: 196px;
    font-family: "Arimo", Arial, sans-serif; font-size: 16px; color: var(--ink);
  }
  .contact__address { line-height: 21px; margin-bottom: 18px; }
  .contact__list { list-style: none; }
  .contact__item { display: flex; align-items: center; height: 23.5px; }
  .contact__icon { width: 13px; height: 13px; margin-right: 6px; fill: var(--navy); flex: none; }
  .contact__dot { width: 12px; height: 12px; border-radius: 50%; background: var(--navy); margin-right: 7px; flex: none; }
</style>
</head>
<body>
  <section class="card card--front">
    <div class="accent-bar"></div>
    <div class="person">
      <h1 class="person__name">DANIEL WHITMORE</h1>
      <p class="person__title">CEO/Founder</p>
    </div>

    <div class="brand brand--front">
      <span class="brand__mark"></span>
      <span class="brand__name">MERIDIAN SERVICE REPS</span>
    </div>

    <div class="contact">
      <p class="contact__address">48 Harbor Lane, Suite 210<br>Lakeview, AB 42190</p>
      <ul class="contact__list">
        <li class="contact__item">
          <svg class="contact__icon" viewBox="0 0 16 16" aria-hidden="true"><path d="M1 6c0-2 3-4 7-4s7 2 7 4v1.5h-3.5V6h-7v1.5H1z"/><rect x="3" y="8" width="10" height="6" rx="1"/></svg>
          555-014-2290
        </li>
        <li class="contact__item">
          <svg class="contact__icon" viewBox="0 0 16 16" aria-hidden="true"><path d="M1 6l7-5 7 5v9H1z M2.5 7v6.5h11V7L8 11z"/></svg>
          hello@meridianservicereps.com
        </li>
        <li class="contact__item">
          <svg class="contact__icon" viewBox="0 0 16 16" aria-hidden="true"><circle cx="8" cy="8" r="7"/><path d="M4 5c2 0 2 2 4 2s1 3-1 3-1 3-3 2z M10 3c1 1 2 1 3 3-1 1-2 0-3-1z" fill="#f4f4f3"/></svg>
          www.meridianservicereps.com
        </li>
        <li class="contact__item">
          <span class="contact__dot"></span>
          @meridianservicereps
        </li>
      </ul>
    </div>
  </section>

  <section class="card card--back">
    <div class="brand brand--back">
      <span class="brand__mark"></span>
      <span class="brand__name">MERIDIAN SERVICE REPS</span>
    </div>
  </section>
</body>
</html>
```